Card design for orthopaedic surgeons working as The Brightwater Joint Centre

Business cards, letterhead

Colors

Designer to choose colors to be used in the design.

Requirements
Must have
• Late addition.
• Cards letterhead must have logos of
• Crestmoor Lindell College of Surgeons
• Varenwood Bone Health Association
Nice to have
• Back of card to have space for appointment time to be added by hand and some blank space for writing incidental other notes.

```html
<!DOCTYPE html>
<html lang="en">
<head>
<meta charset="utf-8">
<title>The Brightwater Joint Centre – Business Card</title>
<link href="https://fonts.googleapis.com/css2?family=Roboto:wght@400;500&display=swap" rel="stylesheet">
<style>
  :root {
    --page-bg: #c9c9c9;
    --card-white: #ffffff;
    --card-navy: #143f56;
    --sky: #4aa3dc;
    --ink: #2b3b47;
    --rule: #1d3f55;
  }
  html, body {
    margin: 0;
    padding: 0;
    width: 1125px;
    height: 1200px;
    overflow: hidden;
    background: var(--page-bg);
    font-family: "Roboto", Arial, sans-serif;
  }
  .canvas {
    position: relative;
    width: 1125px;
    height: 1200px;
  }
  .card {
    position: absolute;
    left: 150px;
    width: 825px;
    height: 470px;
    border-radius: 24px;
    overflow: hidden;
  }
  .card--front { top: 98px; background: var(--card-white); }
  .card--back { top: 631px; background: var(--card-navy); }

  .brand-name {
    position: absolute;
    margin: 0;
    font-weight: 400;
    white-space: nowrap;
    letter-spacing: -0.3px;
  }
  .card--front .brand-name {
    left: 217px;
    top: 247px;
    transform: translate(-50%, -50%);
    font-size: 21px;
    color: var(--sky);
  }
  .card--back .brand-name {
    left: 50%;
    top: 234px;
    transform: translate(-50%, -50%);
    font-size: 34px;
    color: #ffffff;
  }

  .divider {
    position: absolute;
    left: 412px;
    top: 165px;
    width: 2px;
    height: 140px;
    background: var(--rule);
  }
  .contact-block {
    position: absolute;
    left: 453px;
    top: 161px;
  }
  .person-name {
    margin: 0;
    font-size: 31px;
    font-weight: 500;
    color: var(--sky);
    line-height: 36px;
  }
  .person-role {
    margin: 0 0 20px;
    font-size: 18px;
    color: var(--ink);
    line-height: 22px;
  }
  .contact-list {
    list-style: none;
    margin: 0;
    padding: 0;
  }
  .contact-list li {
    display: flex;
    align-items: center;
    gap: 8px;
    font-size: 18.5px;
    line-height: 24px;
    color: var(--ink);
  }
  .contact-list svg { width: 14px; height: 14px; flex: none; fill: var(--sky); }
  .accent { color: var(--sky); }

  .address {
    position: absolute;
    left: 0;
    right: 0;
    top: 418px;
    margin: 0;
    text-align: center;
    font-size: 18.5px;
    color: var(--ink);
  }
</style>
</head>
<body>
<div class="canvas">

  <section class="card card--front">
    <p class="brand-name">The Brightwater Joint Centre</p>
    <div class="divider"></div>
    <div class="contact-block">
      <h1 class="person-name">Alex Marlow</h1>
      <p class="person-role">Manager</p>
      <ul class="contact-list">
        <li>
          <svg viewBox="0 0 24 24" aria-hidden="true"><path d="M6.6 10.8a15 15 0 0 0 6.6 6.6l2.2-2.2a1 1 0 0 1 1-.25 11.4 11.4 0 0 0 3.6.57 1 1 0 0 1 1 1V20a1 1 0 0 1-1 1A17 17 0 0 1 3 4a1 1 0 0 1 1-1h3.5a1 1 0 0 1 1 1c0 1.25.2 2.45.57 3.6a1 1 0 0 1-.25 1z"/></svg>
          123-456-2100
        </li>
        <li>
          <svg viewBox="0 0 24 24" aria-hidden="true"><path d="M2 6h20v12H2z" fill="none"/><path d="M2 5h20v14H2zM4 7l8 5 8-5" style="fill:var(--sky)"/><path d="M4 8l8 5 8-5" stroke="#fff" stroke-width="1.6" fill="none"/></svg>
          youremail@mailbox.com
        </li>
        <li>
          <svg viewBox="0 0 24 24" aria-hidden="true"><circle cx="12" cy="12" r="10"/><path d="M2 12h20M12 2c3 3 3 17 0 20M12 2c-3 3-3 17 0 20" stroke="#fff" stroke-width="1.5" fill="none"/></svg>
          www.<span class="accent">yourwebsite</span>.com
        </li>
      </ul>
    </div>
    <p class="address">Your address, city, state, ZIP 0000</p>
  </section>

  <section class="card card--back">
    <p class="brand-name">The Brightwater Joint Centre</p>
  </section>

</div>
</body>
</html>
```